Direct to Consumer extended service contract business with a new disruptive business model needs a

We need a customized wordpress design for a company called 'Bright Harbor Assurance'.
We provide an innovative and unique service contract protection program direct to consumers. This program provides monthly coverage for all electronics purchased in the last 4 years and all electronics the consumer purchases in the future for a low monthly fee. The overall design should communicate a sense of legitimacy, ethics, and superior customer service and support (in an industry that has a huge PR issue to overcome).
Electronics is the first product group, other product groups with different price points to launch in the future..

Target Market(s)

All purchasers of electronic goods...all demographics

Industry/Entity Type

Electronics

Font styles to use
Sans Serif

Requirements
Must have
• Customer Testimonials
Industry News
Customer ratings
Blog posts
Call to action messaging
Like the functional elements and design of quillmesa.example (need to be better)
Nice to have
• Like to see video testimonials
Social network "whats trending related to electronics or service contract industry"
Easy way to register products for warranty

```html
<!DOCTYPE html>
<html lang="en">
<head>
<meta charset="utf-8">
<title>Bright Harbor Assurance</title>
<link rel="stylesheet" href="https://fonts.googleapis.com/css2?family=Cabin:wght@400;500;600;700&display=swap">
<style>
:root{
  --dark:#2d241b;
  --dark-2:#3a3026;
  --gold:#d9a520;
  --gold-light:#f0c040;
  --ink:#1d1d1d;
  --muted:#555;
  --green-band:#a9bb86;
  --green-box:#8ea06a;
  --tile:#3fae5a;
  --tile-light:#63c67a;
  --link-green:#3a9a52;
  --beige:#d8c8b0;
  --white:#fff;
}
*{box-sizing:border-box;margin:0;padding:0}
html,body{width:1200px;height:4245px;overflow:hidden}
body{font-family:"Cabin",Arial,sans-serif;color:var(--ink);background:var(--white);position:relative}
.abs{position:absolute}
.hero{left:0;top:0;width:1200px;height:487px;background:radial-gradient(ellipse at 50% 40%,#6a5844 0%,#3d3125 55%,#221a12 100%)}
.hero-name{left:0;top:330px;width:1200px;text-align:center;font-size:54px;font-weight:700;letter-spacing:4px;color:#e9dcc0;text-transform:uppercase}
.navbar{left:0;top:487px;width:1200px;height:56px;background:linear-gradient(#e6b42c,#c99414)}
.nav-brand{left:0;top:0;width:240px;height:56px;background:var(--dark);display:flex;align-items:center;gap:10px;padding-left:18px;color:var(--gold-light);font-weight:700;font-size:15px;text-transform:uppercase;line-height:1.05}
.nav-brand .dot{width:22px;height:22px;background:var(--gold);flex:none}
.nav-links{left:334px;top:0;height:56px;display:flex;align-items:center;gap:42px;list-style:none;font-size:15px;font-weight:600;color:var(--white);text-transform:uppercase}
.util{right:30px;top:550px;display:flex;gap:28px;font-size:15px;color:var(--link-green)}
.section-title{position:absolute;left:0;width:1200px;text-align:center;font-size:52px;font-weight:500;text-transform:uppercase;letter-spacing:1px}
.section-sub{position:absolute;left:300px;width:600px;text-align:center;font-size:21px;line-height:1.35}
.diagram{left:0;top:720px}
.dlabel{font-family:"Cabin",Arial,sans-serif;fill:var(--ink)}
.plans{left:0;top:1188px;width:1200px;height:646px;background:var(--dark)}
.plan{top:190px;width:260px;height:394px;background:var(--white);border:6px double var(--gold);outline:4px solid var(--dark);text-align:center;padding:24px 20px}
.plan h3{font-size:44px;font-weight:500;letter-spacing:1px}
.plan p{font-size:22px;line-height:1.36;margin-top:18px}
.plan .price{font-size:44px;margin-top:22px}
.plan .buy{font-size:22px;margin-top:4px}
.devices{left:80px;top:2052px;width:395px;height:368px;background:linear-gradient(135deg,#cfd8e2,#5d8fb8 55%,#2c2f35)}
.quote{left:572px;top:2052px;width:583px;height:353px;border:2px solid #bdbdbd;padding:28px 34px}
.quote h3{font-size:36px;font-weight:500;text-align:center}
.select{height:54px;border:2px solid #999;margin-top:14px;display:flex;align-items:center;justify-content:space-between;padding:0 16px;font-size:24px}
.select svg{width:28px;height:16px}
.quote .btn{margin-top:18px;height:56px;background:linear-gradient(#efbd36,#cf9a16);font-size:34px;font-weight:600;text-align:center;line-height:56px}
.rating{left:0;top:2440px;width:1200px;height:687px;background:var(--green-band)}
.store{top:215px;width:314px;height:133px;background:var(--green-box);border:2px solid #7a8b58;display:flex;gap:16px;padding:16px 14px;align-items:center}
.store .mark{width:96px;height:96px;border-radius:50%;background:var(--dark);flex:none}
.store h4{font-size:28px;font-weight:500;color:#1e1e1e}
.store p{font-size:13px;line-height:1.2;color:#fff}
.stars{display:flex;gap:4px;margin-top:4px}
.video{top:390px;width:184px;height:184px;border-radius:50%;border:3px solid #6c7b4b;background:radial-gradient(circle,#c9b8a3,#6e5f52)}
.video svg{position:absolute;left:52px;top:52px}
.vcap{top:590px;width:250px;text-align:center;font-size:16px;line-height:1.2}
.tile{width:256px;height:250px;background:linear-gradient(135deg,var(--tile-light),var(--tile) 60%,#2f9a48)}
.tag{position:absolute;right:12px;top:12px;background:linear-gradient(#f0c24a,#c99414);font-size:12px;text-transform:uppercase;padding:2px 14px;color:#3a2a00}
.ptitle{width:260px;text-align:center;font-size:16px;color:var(--link-green);text-transform:uppercase}
.footer{left:0;top:3962px;width:1200px;height:255px;background:var(--beige)}
.fcol h5{font-size:18px;font-weight:700;text-transform:uppercase;border-bottom:2px solid #555;padding-bottom:8px;width:230px}
.fcol ul{list-style:none;font-size:15px;line-height:1.35}
.feed-item{display:flex;gap:10px;align-items:center;margin-top:8px}
.feed-item .av{width:42px;height:42px;border-radius:50%;background:#d2541c;flex:none}
.feed-item b{display:block;font-size:10px;color:#c0392b;text-transform:uppercase}
.feed-item span{font-size:10px}
.copy{left:0;top:4217px;width:1200px;height:28px;background:var(--dark);color:#fff;text-align:center;font-size:14px;line-height:28px}
</style>
</head>
<body>

<header>
  <div class="abs hero" role="img" aria-label="Dark textured leather background behind the brand name"></div>
  <div class="abs hero-name">Bright Harbor Assurance</div>
  <nav class="abs navbar">
    <div class="abs nav-brand"><span class="dot"></span><span>Bright Harbor<br>Assurance</span></div>
    <ul class="abs nav-links"><li>Home</li><li>About Us</li><li>Plans</li><li>Take Action</li><li>Blog</li><li>News</li><li>FAQ</li><li>Contact Us</li></ul>
  </nav>
  <div class="abs util"><span>● log in</span><span>( support</span></div>
</header>

<section class="what-we-do">
  <h2 class="section-title" style="top:590px">What We Do</h2>
  <p class="section-sub" style="top:655px">Lorem ipsum nipsum saye losamu Lorem ipsum nipsum saye losamu Lorem ipsum nipsum saye losamu</p>
  <svg class="abs" style="left:0;top:720px" width="1200" height="470" viewBox="0 720 1200 470">
    <g stroke="#222" stroke-width="3" fill="none">
      <polyline points="142,843 439,957 764,900 1075,1036"/>
      <line x1="142" y1="843" x2="249" y2="812"/>
      <line x1="142" y1="843" x2="170" y2="962"/>
      <line x1="439" y1="957" x2="470" y2="862"/>
      <line x1="439" y1="957" x2="552" y2="1056"/>
      <line x1="1075" y1="1036" x2="1075" y2="849"/>
      <line x1="1075" y1="1036" x2="962" y2="1087"/>
    </g>
    <g fill="#222">
      <circle cx="249" cy="812" r="20"/><circle cx="170" cy="962" r="20"/>
      <circle cx="470" cy="862" r="20"/><circle cx="552" cy="1056" r="20"/>
      <circle cx="1075" cy="849" r="20"/><circle cx="962" cy="1087" r="20"/>
    </g>
    <g fill="var(--dark)" stroke="var(--gold)" stroke-width="5">
      <circle cx="142" cy="843" r="62"/><circle cx="439" cy="957" r="55"/>
      <circle cx="764" cy="900" r="62"/><circle cx="1075" cy="1036" r="55"/>
    </g>
    <rect x="112" y="825" width="60" height="36" rx="14" fill="var(--gold)"/>
    <text x="439" y="975" text-anchor="middle" font-size="50" font-weight="700" fill="var(--gold)" font-family="Cabin,sans-serif">$</text>
    <path d="M736 875 H792 V905 Q792 930 764 942 Q736 930 736 905 Z" fill="var(--gold)"/>
    <rect x="1050" y="1011" width="50" height="50" rx="6" fill="none" stroke="var(--gold)" stroke-width="6"/>
    <g class="dlabel">
      <text x="48" y="775" font-size="28" text-transform="uppercase">PURCHASE</text>
      <text x="272" y="815" font-size="14">LOW</text><text x="272" y="831" font-size="14">RATES</text>
      <text x="130" y="1008" font-size="14">MORE THAN</text><text x="130" y="1024" font-size="14">50000 ITEMS</text>
      <text x="434" y="825" font-size="14">MONTHLY</text>
      <text x="368" y="1050" font-size="28">PAY BILLS</text>
      <text x="518" y="1096" font-size="14">DIFFERENT</text><text x="518" y="1112" font-size="14">PACKAGES</text>
      <text x="700" y="835" font-size="28">PROTECT</text>
      <text x="1026" y="813" font-size="14">CLAIM YOUR</text><text x="1040" y="829" font-size="14">MONEY</text>
      <text x="856" y="1087" font-size="14">FIX YOUR</text><text x="856" y="1103" font-size="14">BROKEN</text><text x="856" y="1119" font-size="14">DEVICE</text>
      <text x="1030" y="1115" font-size="28">CLAIM</text>
    </g>
  </svg>
</section>

<section class="abs plans">
  <h2 class="section-title" style="top:40px;color:#fff">Our Plans</h2>
  <p class="section-sub" style="top:102px;color:#fff">Lorem ipsum nipsum saye losamu Lorem ipsum nipsum saye losamu Lorem ipsum nipsum saye losamu</p>
  <article class="abs plan" style="left:48px"><h3>GOLD</h3><p>Lorem ipsum nipsum saye losamu Lorem ipsum nipsum saye losamu Lorem ipsum nipsum saye losamu</p><div class="price">$79/M</div><div class="buy">BUY NOW</div></article>
  <article class="abs plan" style="left:325px"><h3>SILVER</h3><p>Lorem ipsum nipsum saye losamu Lorem ipsum nipsum saye losamu Lorem ipsum nipsum saye losamu</p><div class="price">$179/M</div><div class="buy">BUY NOW</div></article>
  <article class="abs plan" style="left:606px"><h3>BEST</h3><p>Lorem ipsum nipsum saye losamu Lorem ipsum nipsum saye losamu Lorem ipsum nipsum saye losamu</p><div class="price">$109/M</div><div class="buy">BUY NOW</div></article>
  <article class="abs plan" style="left:886px"><h3>SUPERB</h3><p>Lorem ipsum nipsum saye losamu Lorem ipsum nipsum saye losamu Lorem ipsum nipsum saye losamu</p><div class="price">$379/M</div><div class="buy">BUY NOW</div></article>
</section>

<section class="take-action">
  <h2 class="section-title" style="top:1895px">Take Action Now</h2>
  <p class="section-sub" style="top:1955px;left:200px;width:800px">“Pay Less and Claim more on your electronic device Insurance”</p>
  <div class="abs devices" role="img" aria-label="Desktop monitor, tablet and phone showing the website"></div>
  <form class="abs quote">
    <h3>GET A QUOTE TODAY</h3>
    <div class="select">Select your mobile phone<svg viewBox="0 0 28 16"><path d="M0 0H28L14 16Z" fill="#222"/></svg></div>
    <div class="select">Select service provider<svg viewBox="0 0 28 16"><path d="M0 0H28L14 16Z" fill="#222"/></svg></div>
    <div class="btn">GET QUOTE</div>
  </form>
</section>

<section class="abs rating">
  <h2 class="section-title" style="top:70px">Customer Raiting</h2>
  <p class="section-sub" style="top:130px;left:330px;width:540px">Still confused? check what does our royal customer says about our services</p>
  <div class="abs store" style="left:62px"><span class="mark"></span><div><h4>Orchard Store</h4><p>Short notes from buyers who rate our cover and support.</p>
    <svg class="stars" width="130" height="22"><g fill="#d8342c"><circle cx="11" cy="11" r="9"/><circle cx="37" cy="11" r="9"/><circle cx="63" cy="11" r="9"/><circle cx="89" cy="11" r="9"/><circle cx="115" cy="11" r="9"/></g></svg></div></div>
  <div class="abs store" style="left:419px"><span class="mark"></span><div><h4>Riverbend Store</h4><p>Short notes from buyers who rate our cover and support.</p>
    <svg class="stars" width="130" height="22"><g fill="#3c6fd8"><circle cx="11" cy="11" r="9"/><circle cx="37" cy="11" r="9"/><circle cx="63" cy="11" r="9"/><circle cx="89" cy="11" r="9"/><circle cx="115" cy="11" r="9"/></g></svg></div></div>
  <div class="abs store" style="left:781px"><span class="mark" style="background:#d8342c"></span><div><h4>Searchly Store</h4><p>Short notes from buyers who rate our cover and support.</p>
    <svg class="stars" width="130" height="22"><g fill="#4caf50"><circle cx="11" cy="11" r="9"/><circle cx="37" cy="11" r="9"/><circle cx="63" cy="11" r="9"/><circle cx="89" cy="11" r="9"/><circle cx="115" cy="11" r="9"/></g></svg></div></div>
  <div class="abs video" style="left:95px" role="img" aria-label="Video testimonial from a customer"><svg width="80" height="80"><circle cx="40" cy="40" r="36" fill="none" stroke="#fff" stroke-width="5"/><path d="M30 22 L58 40 L30 58Z" fill="#fff"/></svg></div>
  <div class="abs video" style="left:358px" role="img" aria-label="Video testimonial from a customer"><svg width="80" height="80"><circle cx="40" cy="40" r="36" fill="none" stroke="#fff" stroke-width="5"/><path d="M30 22 L58 40 L30 58Z" fill="#fff"/></svg></div>
  <div class="abs video" style="left:618px" role="img" aria-label="Video testimonial from a customer"><svg width="80" height="80"><circle cx="40" cy="40" r="36" fill="none" stroke="#fff" stroke-width="5"/><path d="M30 22 L58 40 L30 58Z" fill="#fff"/></svg></div>
  <div class="abs video" style="left:876px" role="img" aria-label="Video testimonial from a customer"><svg width="80" height="80"><circle cx="40" cy="40" r="36" fill="none" stroke="#fff" stroke-width="5"/><path d="M30 22 L58 40 L30 58Z" fill="#fff"/></svg></div>
  <p class="abs vcap" style="left:62px">some info came here with description, some info came here with description.</p>
  <p class="abs vcap" style="left:325px">some info came here with description, some info came here with description.</p>
  <p class="abs vcap" style="left:585px">some info came here with description, some info came here with description.</p>
  <p class="abs vcap" style="left:843px">some info came here with description, some info came here with description.</p>
</section>

<section class="blog">
  <h2 class="section-title" style="top:3170px">Welcome To Our Blog</h2>
  <p class="section-sub" style="top:3232px">Lorem ipsum nipsum saye losamu Lorem ipsum nipsum saye losamu Lorem ipsum nipsum saye losamu</p>
  <div class="abs tile" style="left:62px;top:3317px" role="img" aria-label="Post image"><span class="tag">News</span></div>
  <div class="abs tile" style="left:334px;top:3317px" role="img" aria-label="Post image"><span class="tag">Opinion</span></div>
  <div class="abs tile" style="left:608px;top:3317px" role="img" aria-label="Post image"><span class="tag">Breaking</span></div>
  <div class="abs tile" style="left:880px;top:3317px" role="img" aria-label="Post image"><span class="tag">Gadgets</span></div>
  <p class="abs ptitle" style="left:60px;top:3574px">Post title will came here</p>
  <p class="abs ptitle" style="left:332px;top:3574px">Post title will came here</p>
  <p class="abs ptitle" style="left:606px;top:3574px">Post title will came here</p>
  <p class="abs ptitle" style="left:878px;top:3574px">Post title will came here</p>
  <div class="abs tile" style="left:62px;top:3620px" role="img" aria-label="Post image"><span class="tag">Category</span></div>
  <div class="abs tile" style="left:334px;top:3620px" role="img" aria-label="Post image"><span class="tag">Category</span></div>
  <div class="abs tile" style="left:608px;top:3620px" role="img" aria-label="Post image"><span class="tag">Category</span></div>
  <div class="abs tile" style="left:880px;top:3620px" role="img" aria-label="Post image"><span class="tag">Category</span></div>
  <p class="abs ptitle" style="left:60px;top:3876px">Post title will came here</p>
  <p class="abs ptitle" style="left:332px;top:3876px">Post title will came here</p>
  <p class="abs ptitle" style="left:606px;top:3876px">Post title will came here</p>
  <p class="abs ptitle" style="left:878px;top:3876px">Post title will came here</p>
</section>

<footer>
  <div class="abs footer">
    <div class="abs fcol" style="left:92px;top:50px"><h5>Welcome to BHA</h5>
      <div style="display:flex;gap:70px;margin-top:14px"><ul><li>Our Plans</li><li>Benefits</li><li>About us</li><li>Contact us</li></ul><ul><li>Blog</li><li>News</li><li>Support</li><li>Terms</li></ul></div></div>
    <div class="abs fcol" style="left:424px;top:50px"><h5 style="border:none;display:flex;gap:8px;align-items:center">Social Media Feed
      <svg width="100" height="34"><rect x="0" y="2" width="30" height="30" fill="#3b5998"/><rect x="34" y="2" width="30" height="30" fill="#3fa9e0"/><rect x="68" y="2" width="30" height="30" fill="#c4302b"/></svg></h5>
      <div style="background:#fff;width:310px;padding:6px 10px;margin-top:4px">
        <div class="feed-item"><span class="av"></span><div><b>Name of person</b><span>This is a sample post from a social feed.</span></div></div>
        <div class="feed-item"><span class="av"></span><div><b>Name of person</b><span>This is a sample post from a social feed.</span></div></div>
        <div class="feed-item"><span class="av"></span><div><b>Name of person</b><span>This is a sample post from a social feed.</span></div></div>
      </div></div>
    <div class="abs fcol" style="left:822px;top:50px"><h5>Contact Us</h5>
      <ul style="margin-top:14px;padding-left:34px;font-size:13px;line-height:1.4"><li>48 Lantern Row</li><li>Fairhaven 2210</li><li>Ph: (000) 555-0148</li><li>Email: hello@brightharbor.example</li></ul></div>
  </div>
  <div class="abs copy">Copyright © 2014 Bright Harbor Assurance</div>
</footer>

</body>
</html>
```